Business Card - Tidal Lanes

Need Business Card design for company named Tidal Lanes. Software development focused mainly on Brindle Orvix & Zelt Apps. I've attached our logo with both a black and white background. Please add trademark symbol to logo when using.

```html
<!DOCTYPE html>
<html lang="en">
<head>
<meta charset="utf-8">
<title>Tidal Lanes – Business Card</title>
<link rel="stylesheet" href="https://fonts.googleapis.com/css2?family=Open+Sans:wght@400;600;700&display=swap">
<style>
  :root {
    --page-bg: #e9e6e1;
    --card-black: #050505;
    --accent-red: #d6202a;
    --sun-yellow: #f8c219;
    --sun-orange: #f3962e;
    --ink-dark: #1e1a12;
    --paper-white: #ffffff;
  }
  * { box-sizing: border-box; margin: 0; padding: 0; }
  html, body {
    width: 1200px; height: 720px; overflow: hidden;
    background: var(--page-bg);
    font-family: "Open Sans", Arial, sans-serif;
  }
  .sheet {
    position: relative; width: 1200px; height: 720px;
    display: flex; align-items: center; justify-content: center; gap: 50px;
  }
  .card {
    position: relative; width: 525px; height: 300px; overflow: hidden;
    box-shadow: 0 6px 18px rgba(0,0,0,.18);
  }
  .card__art { position: absolute; inset: 0; width: 100%; height: 100%; }

  /* Front */
  .brand {
    position: absolute; top: 86px; left: 0; width: 100%;
    text-align: center; color: var(--paper-white);
    font-weight: 700; font-size: 30px; letter-spacing: -0.5px;
  }
  .contact {
    position: absolute; top: 196px; left: 120px;
    display: flex; align-items: flex-start; color: var(--ink-dark);
  }
  .contact__person {
    text-align: right; padding-right: 12px; padding-top: 22px;
    border-right: 1px solid rgba(30,26,18,.5); height: 62px;
  }
  .contact__name { font-weight: 700; font-size: 17px; line-height: 1.1; }
  .contact__title { font-size: 13px; }
  .contact__details { padding-left: 12px; font-size: 13.5px; line-height: 1.55; }
  .contact__line { display: flex; align-items: center; gap: 6px; }
  .contact__icon { width: 11px; height: 13px; flex: none; }
  .contact__address { font-size: 12px; margin-top: 2px; }

  /* Back */
  .card--back {
    background: linear-gradient(115deg, var(--sun-yellow) 0%, var(--sun-orange) 100%);
    display: flex; align-items: center; justify-content: center;
  }
  .card--back .brand {
    position: static; width: auto; font-size: 48px;
  }
</style>
</head>
<body>
<main class="sheet">

  <section class="card card--front" aria-label="Business card front">
    <svg class="card__art" viewBox="0 0 525 300" preserveAspectRatio="none" aria-hidden="true">
      <defs>
        <linearGradient id="sunFill" x1="0" y1="0" x2="1" y2="0">
          <stop offset="0" stop-color="#f8c219"/>
          <stop offset="1" stop-color="#f3962e"/>
        </linearGradient>
      </defs>
      <rect width="525" height="300" fill="url(#sunFill)"/>
      <path d="M0 0 H525 V152 C360 160 170 190 0 238 Z" fill="#050505"/>
      <path d="M0 238 C170 190 360 160 525 152" fill="none" stroke="#d6202a" stroke-width="5"/>
    </svg>

    <div class="brand">Tidal Lanes</div>

    <div class="contact">
      <div class="contact__person">
        <div class="contact__name">Your Name</div>
        <div class="contact__title">Title</div>
      </div>
      <div class="contact__details">
        <div class="contact__line">
          <svg class="contact__icon" viewBox="0 0 11 13" aria-hidden="true"><rect x="2" y="0.5" width="7" height="12" rx="1.5" fill="none" stroke="#1e1a12" stroke-width="1.3"/><circle cx="5.5" cy="10.3" r="0.9" fill="#1e1a12"/></svg>
          <span>555-204-1180</span>
        </div>
        <div class="contact__line">
          <svg class="contact__icon" viewBox="0 0 11 13" aria-hidden="true"><path d="M2 1.5 L4 1 L5 4 L3.8 5 Q4.8 7.6 6.8 8.8 L8 7.8 L10.6 9 L10 11.2 Q5 12 1.6 5.5 Q1.2 3 2 1.5 Z" fill="#1e1a12"/></svg>
          <span>555-317-6642</span>
        </div>
        <div class="contact__address">4210 Harbor Row, Marlow, FL 30012</div>
      </div>
    </div>
  </section>

  <section class="card card--back" aria-label="Business card back">
    <div class="brand">Tidal Lanes</div>
  </section>

</main>
</body>
</html>
```